The Copperline Collective's website for high impact furniture promotions

I am looking for a simple website. we are a promotional company that runs events for furniture stores to increase sales for short periods of time. i would like the website to have about 4 areas to explain our company. I would like it to be simple and user friendly. I would like a link to chatterbook and a contact section. I am attaching our logo that i would like somewhere large or possibly in the backround. I am open to different color schemes. I would like to convey fast paced, modern, reliable. I am open to all different styles and look forward to seeing whats out there. we are looking for a quick turn around, so if we see one that we like quick, we will pick that one thanks
Reason: looking for some really creative designs and want to give a fair amount of time to produce
Target Market(s)
Retail Furniture store owners
Industry/Entity Type
It Company
Number of Pages Required
1 page
Colors
Designer to choose colors to be used in the design.
Look and feel

```html
<!DOCTYPE html>
<html lang="en">
<head>
<meta charset="utf-8">
<title>The Copperline Collective — High Impact Furniture Promotions</title>
<link href="https://fonts.googleapis.com/css2?family=Noto+Serif:ital,wght@0,400;0,700;1,400&family=Open+Sans:ital,wght@0,400;0,600;0,700;1,400;1,700&display=swap" rel="stylesheet">
<style>
:root{
  --copper:#8b5a32;
  --copper-dark:#6f4526;
  --tan:#c79a6a;
  --ink:#2b2b2b;
  --muted:#666;
  --paper:#ffffff;
  --footer:#f1f1f1;
  --night:#221d18;
}
*{box-sizing:border-box;margin:0;padding:0}
html,body{width:1200px;height:3056px;overflow:hidden}
body{position:relative;font-family:"Open Sans",Arial,sans-serif;color:var(--ink);background:var(--paper)}

/* header */
.site-header{position:absolute;left:0;top:0;width:1200px;height:90px;background:var(--paper);z-index:5}
.nav-link{position:absolute;top:36px;font-family:"Noto Serif",Georgia,serif;font-size:14px;letter-spacing:.5px;color:var(--ink);text-transform:uppercase}
.brand-badge{position:absolute;left:478px;top:20px;width:244px;height:128px;background:var(--paper);border-radius:0 0 122px 122px;z-index:6;text-align:center}
.brand-dot{width:46px;height:46px;border-radius:50%;background:var(--copper);margin:0 auto}
.brand-name{margin-top:10px;font-family:"Noto Serif",Georgia,serif;font-size:15px;line-height:18px;color:var(--copper);text-transform:uppercase;letter-spacing:1.5px}

/* hero */
.hero{position:absolute;left:0;top:90px;width:1200px;height:600px}
.hero-photo{position:absolute;inset:0;background:linear-gradient(100deg,#6d6a66 0%,#a49a90 35%,#8d8379 60%,#5d5750 100%)}
.hero-title{position:absolute;left:98px;top:264px;font-family:"Noto Serif",Georgia,serif;font-weight:700;font-size:56px;line-height:58px;color:#fff}
.hero-dots{position:absolute;left:100px;top:396px;display:flex;gap:5px}
.hero-dots span{width:14px;height:14px;border-radius:50%;border:2px solid #fff}
.hero-dots span.on{background:#fff}
.quick-contact{position:absolute;left:805px;top:155px;width:297px;height:350px;background:rgba(30,28,26,.85)}
.qc-icon{position:absolute;left:120px;top:-20px;width:56px;height:56px;border-radius:50%;background:rgba(30,28,26,.95)}
.qc-title{position:absolute;left:0;width:100%;top:48px;text-align:center;font-family:"Noto Serif",Georgia,serif;font-weight:700;font-size:32px;color:#fff}
.qc-field{position:absolute;left:22px;width:253px;height:38px;background:#fff;font-size:12px;color:#777;padding:11px 10px}
.qc-submit{position:absolute;left:22px;top:293px;width:253px;height:31px;background:var(--tan);color:#fff;font-size:13px;text-align:center;line-height:31px;text-transform:uppercase}

/* welcome */
.welcome{position:absolute;left:0;top:690px;width:1200px;height:472px;background:var(--copper)}
.welcome-title{position:absolute;left:0;width:100%;top:72px;text-align:center;font-family:"Noto Serif",Georgia,serif;font-weight:700;font-size:38px;color:#fff}
.welcome-copy{position:absolute;left:155px;width:890px;top:138px;text-align:center;font-size:11px;line-height:23px;color:#f3e6d8}
.feature{position:absolute;top:265px;width:330px}
.feature-icon{position:absolute;left:0;top:0;width:72px;height:72px;border-radius:50%;background:var(--tan);border:5px solid #a8774c}
.feature-icon svg{position:absolute;left:17px;top:17px}
.feature-title{position:absolute;left:96px;top:6px;font-family:"Noto Serif",Georgia,serif;font-size:17px;color:#fff;white-space:nowrap}
.feature-copy{position:absolute;left:96px;top:37px;width:220px;font-size:11px;line-height:20px;color:#f3e6d8}
.feature-more{position:absolute;left:96px;top:106px;font-size:11px;color:#fff;text-transform:uppercase;font-weight:600}

/* promotional */
.promo-title{position:absolute;left:0;width:1200px;top:1226px;text-align:center;font-family:"Noto Serif",Georgia,serif;font-weight:700;font-size:30px;color:var(--copper);letter-spacing:1px}
.promo-tile{position:absolute}
.promo-label{position:absolute;left:50%;top:50%;transform:translate(-50%,-50%);background:rgba(30,28,26,.8);color:#fff;font-size:16px;padding:3px 14px;white-space:nowrap}

/* testimonials */
.testimonials{position:absolute;left:0;top:1783px;width:1200px;height:473px;background:linear-gradient(180deg,#2a241e,#3b342d 50%,#2a2520)}
.testi-frame{position:absolute;left:136px;top:95px;width:927px;height:276px;border:1px solid rgba(255,255,255,.55)}
.testi-title{position:absolute;left:0;width:100%;top:30px;text-align:center;font-family:"Noto Serif",Georgia,serif;font-size:32px;color:#fff;letter-spacing:1px}
.testi-rule{position:absolute;left:418px;top:84px;width:92px;height:2px;background:#fff}
.testi-quote{position:absolute;left:60px;width:807px;top:116px;text-align:center;font-style:italic;font-size:12.5px;line-height:22px;color:#fff}
.testi-name{position:absolute;left:0;width:100%;top:198px;text-align:center;font-style:italic;font-weight:700;font-size:16px;color:#fff}
.testi-dots{position:absolute;left:0;width:100%;top:243px;display:flex;justify-content:center;gap:6px}
.testi-dots span{width:24px;height:3px;background:rgba(255,255,255,.4)}
.testi-dots span.on{background:#fff}

/* events */
.events-title{position:absolute;left:98px;top:2345px;font-family:"Noto Serif",Georgia,serif;font-weight:700;font-size:26px;color:var(--ink)}
.events-title em{font-style:normal;color:var(--copper)}
.events-arrows{position:absolute;left:1070px;top:2350px}
.event-photo{position:absolute;width:187px;height:163px;border:3px solid #eee}
.event-head{position:absolute;font-size:16px;color:var(--ink);width:290px}
.event-date{position:absolute;font-family:"Noto Serif",Georgia,serif;font-size:15px;color:var(--copper)}
.event-copy{position:absolute;width:285px;font-size:11px;line-height:20px;color:var(--muted)}
.event-more{position:absolute;font-size:11px;color:var(--ink);text-transform:uppercase}

/* footer */
.site-footer{position:absolute;left:0;top:2694px;width:1200px;height:298px;background:var(--footer)}
.foot-brand{position:absolute;left:120px;top:44px;width:160px;text-align:center}
.foot-brand .brand-dot{width:58px;height:58px}
.foot-brand .brand-name{font-size:16px;line-height:20px}
.social{position:absolute;left:120px;top:192px;display:flex;align-items:center;gap:8px}
.social-dot{width:14px;height:14px;border-radius:50%;background:var(--copper)}
.social-name{font-family:"Noto Serif",Georgia,serif;font-weight:400;font-size:16px;color:var(--ink)}
.foot-head{position:absolute;top:52px;font-family:"Noto Serif",Georgia,serif;font-size:15px;color:var(--ink);text-transform:uppercase}
.foot-line{position:absolute;font-size:12.5px;color:#555;line-height:20px}
.foot-line svg{position:absolute;left:-26px;top:3px}
.news-input{position:absolute;left:654px;top:140px;width:245px;height:44px;background:#fff;border:1px solid #ddd;font-size:11px;color:#666;padding:14px 12px}
.news-btn{position:absolute;left:654px;top:190px;width:124px;height:38px;background:var(--copper);color:#fff;font-size:15px;font-weight:700;text-align:center;line-height:38px}
.quick-links{position:absolute;left:988px;top:96px;list-style:none}
.quick-links li{font-size:11.5px;color:#555;line-height:26px;padding-left:18px;position:relative}
.quick-links li::before{content:"";position:absolute;left:0;top:9px;border-left:6px solid #444;border-top:4px solid transparent;border-bottom:4px solid transparent}
.copyright{position:absolute;left:0;top:2992px;width:1200px;height:64px;background:var(--paper);border-top:1px solid #ddd;text-align:center;line-height:64px;font-size:11.5px;color:#555}
</style>
</head>
<body>

<header class="site-header">
  <a class="nav-link" style="left:98px">Home</a>
  <a class="nav-link" style="left:198px">Promotional</a>
  <a class="nav-link" style="left:346px">Gallery</a>
  <a class="nav-link" style="left:815px">Review</a>
  <a class="nav-link" style="left:923px">Explore</a>
  <a class="nav-link" style="left:1037px">Contact</a>
</header>
<div class="brand-badge">
  <div class="brand-dot"></div>
  <div class="brand-name">The Copperline<br>Collective</div>
</div>

<section class="hero">
  <div class="hero-photo" role="img" aria-label="Shopper holding a cushion while browsing sofas in a furniture showroom"></div>
  <h1 class="hero-title">Copperline<br>Collective</h1>
  <div class="hero-dots"><span class="on"></span><span></span><span></span></div>
  <form class="quick-contact">
    <div class="qc-icon">
      <svg width="56" height="56" viewBox="0 0 56 56"><circle cx="28" cy="28" r="11" fill="none" stroke="#fff" stroke-width="2"/><path d="M28 22v11M23.5 29l4.5 4.5 4.5-4.5" fill="none" stroke="#fff" stroke-width="2"/></svg>
    </div>
    <div class="qc-title">Quick Contact</div>
    <div class="qc-field" style="top:95px">Name :</div>
    <div class="qc-field" style="top:144px">E- Mail :</div>
    <div class="qc-field" style="top:195px">Phone :</div>
    <div class="qc-field" style="top:244px">Message</div>
    <div class="qc-submit">Submit Now!</div>
  </form>
</section>

<section class="welcome">
  <h2 class="welcome-title">Welcome to Copperline Collective</h2>
  <p class="welcome-copy">Sed ut perspiciatis unde omnis iste natus error sit voluptatem accusantium doloremque laudantium, totam rem aperiam, eaque ipsa quae ab illo inventore veritatis et quasi architecto beatae vitae dicta sunt explicabo. Nemo enim ipsam voluptatem quia voluptas sit aspernatur aut odit aut fugit, sed quia consequuntur magni dolores eos qui ratione voluptatem sequi nesciunt. Neque porro quisquam est, qui dolorem ipsum quia dolor sit amet, consectetur, adipisci velit, sed quia non numquam</p>

  <div class="feature" style="left:98px">
    <div class="feature-icon"><svg width="28" height="28" viewBox="0 0 28 28"><path d="M4 11h5l10-6v18L9 17H4z" fill="#fff"/><path d="M8 17l2 6h3l-2-6z" fill="#fff"/></svg></div>
    <div class="feature-title">Nemo enim ipsam</div>
    <div class="feature-copy">Sed ut perspiciatis unde omnis iste natus error sit voluptatem accusantium doloremque laudantium</div>
    <div class="feature-more">Read more &#9656;</div>
  </div>
  <div class="feature" style="left:450px">
    <div class="feature-icon"><svg width="28" height="28" viewBox="0 0 28 28"><path d="M3 4h11l11 11-10 10L4 14z" fill="#fff"/><circle cx="9" cy="9" r="2.2" fill="#c79a6a"/></svg></div>
    <div class="feature-title">Nemo enim ipsam</div>
    <div class="feature-copy">Sed ut perspiciatis unde omnis iste natus error sit voluptatem accusantium doloremque laudantium</div>
    <div class="feature-more">Read more &#9656;</div>
  </div>
  <div class="feature" style="left:803px">
    <div class="feature-icon"><svg width="28" height="28" viewBox="0 0 28 28"><rect x="3" y="6" width="22" height="19" fill="#fff"/><rect x="3" y="6" width="22" height="5" fill="#eee"/><path d="M6 14h4v3H6zM12 14h4v3h-4zM18 14h4v3h-4zM6 19h4v3H6zM12 19h4v3h-4z" fill="#c79a6a"/><path d="M8 3v5M20 3v5" stroke="#fff" stroke-width="2"/></svg></div>
    <div class="feature-title">Nemo enim ipsam</div>
    <div class="feature-copy">Sed ut perspiciatis unde omnis iste natus error sit voluptatem accusantium doloremque laudantium</div>
    <div class="feature-more">Read more &#9656;</div>
  </div>
</section>

<h2 class="promo-title">OUR PROMOTIONAL</h2>
<div class="promo-tile" style="left:98px;top:1312px;width:336px;height:378px;background:linear-gradient(160deg,#b9b4ab,#8a8a6c 60%,#6a5d58)" role="img" aria-label="Busy furniture store aisle with sofas on display">
  <span class="promo-label">Nemo Enim Ipsam</span>
</div>
<div class="promo-tile" style="left:452px;top:1312px;width:648px;height:200px;background:linear-gradient(180deg,#c9c4bb,#8b6e55 60%,#6b4d3a)" role="img" aria-label="Wide furniture showroom floor filled with dining sets">
  <span class="promo-label">Nemo Enim Ipsam</span>
</div>
<div class="promo-tile" style="left:452px;top:1524px;width:312px;height:166px;background:linear-gradient(180deg,#9a968f,#d8d4cc 45%,#4f7a2f 80%)" role="img" aria-label="Sofa and wooden coffee table on a green rug">
  <span class="promo-label">Nemo Enim Ipsam</span>
</div>
<div class="promo-tile" style="left:776px;top:1524px;width:324px;height:166px;background:linear-gradient(180deg,#5e6678,#b8bcc4 55%,#d7d6d2)" role="img" aria-label="Bright showroom with grey upholstered furniture">
  <span class="promo-label">Nemo Enim Ipsam</span>
</div>

<section class="testimonials" role="img" aria-label="Dimmed furniture showroom behind the testimonials">
  <div class="testi-frame">
    <h2 class="testi-title">TESTIMONIALS</h2>
    <div class="testi-rule"></div>
    <p class="testi-quote">&ldquo; Sed ut perspiciatis unde omnis iste natus error sit voluptatem accusantium doloremque laudantium, totam rem aperiam, eaque ipsa quae ab illo inventore veritatis et quasi architecto beatae vitae dicta sunt explicabo. Nemo enim ipsam voluptatem quia voluptas sit aspernatur aut odit aut fugit, sed quia consequuntur magni dolores eos qui ratione voluptatem &rdquo;</p>
    <div class="testi-name">Jane Porter - Copperline Collective</div>
    <div class="testi-dots"><span class="on"></span><span></span><span></span></div>
  </div>
</section>

<h2 class="events-title">LATEST <em>EVENTS</em></h2>
<svg class="events-arrows" width="32" height="20" viewBox="0 0 32 20"><path d="M8 3L2 10l6 7M24 3l6 7-6 7" fill="none" stroke="#333" stroke-width="2.2"/></svg>

<div class="event-photo" style="left:98px;top:2425px;background:linear-gradient(160deg,#d8d5cf,#9aa3a8 60%,#6f6a62)" role="img" aria-label="Living room corner with shelving and decor"></div>
<div class="event-head" style="left:312px;top:2420px">Nulla at diam ornare, aliquam urna</div>
<div class="event-date" style="left:312px;top:2458px">JULY 25, 2017</div>
<p class="event-copy" style="left:312px;top:2482px">Nulla at diam ornare, aliquam urna vel, commodo urna. Nam id risus a est luctus consectetur quis eget libero. Suspendisse potenti. Pellentesque habitant morbi tristique senectus</p>
<div class="event-more" style="left:312px;top:2570px">Read more +</div>

<div class="event-photo" style="left:632px;top:2425px;background:linear-gradient(160deg,#c9c3bb,#b73a33 55%,#7a5a48)" role="img" aria-label="Red sofas in a furniture store"></div>
<div class="event-head" style="left:843px;top:2420px">Nulla at diam ornare, aliquam urna</div>
<div class="event-date" style="left:843px;top:2458px">JULY 25, 2017</div>
<p class="event-copy" style="left:843px;top:2482px">Nulla at diam ornare, aliquam urna vel, commodo urna. Nam id risus a est luctus consectetur quis eget libero. Suspendisse potenti. Pellentesque habitant morbi tristique senectus</p>
<div class="event-more" style="left:843px;top:2570px">Read more +</div>

<footer class="site-footer">
  <div class="foot-brand">
    <div class="brand-dot"></div>
    <div class="brand-name">The Copperline<br>Collective</div>
  </div>
  <div class="social"><span class="social-dot"></span><span class="social-name">chatterbook</span></div>

  <div class="foot-head" style="left:320px">Contact Us</div>
  <div class="foot-line" style="left:348px;top:98px">
    <svg width="14" height="16" viewBox="0 0 14 16"><path d="M7 1a5 5 0 0 0-5 5c0 4 5 9 5 9s5-5 5-9a5 5 0 0 0-5-5z" fill="#444"/><circle cx="7" cy="6" r="2" fill="#f1f1f1"/></svg>
    Copperline Collective<br>14 Harrow Lane, Brookfield BF2 7QD
  </div>
  <div class="foot-line" style="left:348px;top:150px">
    <svg width="14" height="14" viewBox="0 0 14 14"><path d="M3 1l3 3-2 2c1 2 2 3 4 4l2-2 3 3-2 2C6 13 1 8 1 3z" fill="#444"/></svg>
    Phone: 555-014-2290
  </div>
  <div class="foot-line" style="left:348px;top:182px">
    <svg width="14" height="12" viewBox="0 0 14 12"><rect x="1" y="2" width="12" height="9" fill="#444"/><path d="M1 2l6 5 6-5" fill="none" stroke="#f1f1f1" stroke-width="1.2"/></svg>
    Email: hello@copperlinecollective.com
  </div>

  <div class="foot-head" style="left:654px">Sign Up for Newsletter</div>
  <div class="foot-line" style="left:654px;top:88px;width:260px;font-size:11.5px">Excepteur sint occaecat cupidatat non proident, sunt in culpa qui officia deserunt</div>
  <div class="news-input">Enter email</div>
  <div class="news-btn">SIGN UP</div>

  <div class="foot-head" style="left:984px">Quick Links</div>
  <ul class="quick-links">
    <li>Home</li><li>About Us</li><li>Promotional</li><li>Testimonials</li><li>Contact Us</li>
  </ul>
</footer>
<div class="copyright">&copy;2017 Copperline Collective, All Rights Reserved.</div>

</body>
</html>
```